2020 Teamwear Price List

Price list of our popular teamwear items that we wholesale to clubs and schools.
looking to create a price list with images, images can be obtained from our website:
www.corvelathletichub.com.au
price list does not have to have lots of details about each product, just a from price. with minimum order etc.
and we can email or post to our clients, so it can be A4 pages/booklet style.
i can also provide images after i choose the design layout we like, so you can just use generic images for now if required.
Updates

Target Market(s)

Clubs and Schools

Font styles to use
Sans Serif

Colors

Designer to choose colors to be used in the design.

Requirements
Must have
• Photo or generated image for each product.
Nice to have
• simple format , easy to read , and easy to update from time to time

```html
<!DOCTYPE html>
<html lang="en">
<head>
<meta charset="utf-8">
<title>Teamwear Price List – Pages 5 &amp; 6</title>
<link href="https://fonts.googleapis.com/css2?family=Lato:wght@400;700;900&family=Exo+2:ital,wght@1,900&family=Bebas+Neue&display=swap" rel="stylesheet">
<style>
:root{
  --stage:#b9bcd3;
  --red:#d0202a;
  --red-dark:#8e1016;
  --black:#111111;
  --grey:#d6d6d6;
  --white:#ffffff;
  --text:#222222;
}
*{box-sizing:border-box;margin:0;padding:0}
html,body{width:1200px;height:1200px;overflow:hidden}
body{background:var(--stage);font-family:'Lato',sans-serif;position:relative;color:var(--text)}
.spread-label{position:absolute;top:18px;left:0;width:1200px;text-align:center;color:var(--white);font-size:38px;font-weight:400;letter-spacing:1px}
.page{position:absolute;top:158px;width:582px;height:822px;background:var(--white);overflow:hidden}
.page--left{left:15px}
.page--right{left:605px}

.masthead{position:absolute;top:0;left:0;width:100%;height:88px;background:var(--black)}
.masthead__red{position:absolute;inset:0}
.brand{position:absolute;top:30px;left:28px;display:flex;align-items:center;gap:8px;color:var(--white);font-weight:900;font-size:26px;letter-spacing:1px}
.brand__dot{width:16px;height:16px;border-radius:50%;background:var(--white)}
.contact{position:absolute;top:16px;left:366px;color:var(--white);font-size:11.5px;line-height:14.5px}
.contact__title{display:block}
.contact__row{display:flex;align-items:center;gap:6px}
.contact__icon{width:9px;height:9px;border-radius:50%;background:var(--red);flex:none}

.title-band{position:absolute;top:88px;left:0;width:100%;height:34px;background:linear-gradient(90deg,var(--black) 0 8%,var(--red) 30%,var(--red));border-top:3px solid var(--black);text-align:center;overflow:hidden}
.title-band h1{font-family:'Exo 2',sans-serif;font-style:italic;font-weight:900;font-size:33px;line-height:30px;color:var(--white);letter-spacing:0.5px}
.terms{position:absolute;top:122px;left:0;width:100%;height:36px;background:var(--grey);text-align:center;font-size:10.5px;line-height:13px;padding-top:5px}

.section-head{position:absolute;top:172px;left:0;width:310px;height:34px;border-bottom:2px solid var(--red);display:flex;align-items:center;padding-left:20px;gap:4px}
.section-head__arrow{width:0;height:0;border-top:10px solid transparent;border-bottom:10px solid transparent;border-left:18px solid var(--red)}
.section-head h2{font-family:'Exo 2',sans-serif;font-style:italic;font-weight:900;font-size:31px;color:var(--red);letter-spacing:0.5px}

.grid{position:absolute;top:222px;left:19px;display:grid;grid-template-columns:repeat(4,129.6px);column-gap:9px;row-gap:13px;grid-auto-rows:172px}
.card{border-left:3px solid var(--red);border-right:3px solid var(--red);display:flex;flex-direction:column;align-items:center;background:var(--white)}
.card__name{width:calc(100% + 6px);margin:0 -3px;height:34px;background:var(--red);color:var(--white);font-size:10px;line-height:10.5px;text-align:center;display:flex;flex-direction:column;justify-content:center;text-transform:uppercase}
.card__name small{font-size:8.5px;text-transform:none}
.card__photo{width:86px;height:88px;margin-top:10px;border-radius:6px}
.card__price{margin-top:auto;margin-bottom:10px;color:var(--red);font-weight:900;font-size:16px}
.card__price sup{font-size:11px;vertical-align:baseline}

.ph-ball{background:radial-gradient(circle at 40% 40%,#fff,#cfd2dc 60%,#8a90a8);border-radius:50%}
.ph-bibs{background:linear-gradient(#e23b2c,#f1a02c 30%,#3b7d3b 50%,#3b3f9c 70%,#f07a23)}
.ph-whistle{background:linear-gradient(135deg,#f2f2f2,#4a4536 60%,#f2f2f2)}
.ph-lanyard{background:radial-gradient(ellipse at center,#fff 45%,#444 48%,#fff 55%)}
.ph-comp{background:linear-gradient(#e6e6e6,#9da3ab)}
.ph-heavy{background:linear-gradient(#2f6f5d,#e2532d)}
.ph-pump{background:linear-gradient(160deg,#fff 30%,#f4d32a 45%,#222 60%,#fff 70%)}
.ph-net{background:linear-gradient(#f2c9c9,#2d2d2d)}
.ph-kit{background:linear-gradient(#fff 20%,#1a1a1a 35%,#1a1a1a 80%,#fff 90%)}
.ph-board{background:linear-gradient(#eeeeee,#bdbdbd)}
.ph-tackle{background:linear-gradient(90deg,#fff 35%,#1a3fc4 35% 65%,#fff 65%)}
.ph-bump{background:linear-gradient(90deg,#fff 15%,#1c37a8 15% 85%,#fff 85%)}
.ph-cones{background:linear-gradient(90deg,#f2ea2a,#3a7fd6 50%,#e5322b)}

.footer{position:absolute;left:0;bottom:0;width:100%;height:50px;border-top:4px solid var(--black);background:linear-gradient(90deg,var(--black),var(--red) 45%,var(--red));color:var(--white);text-align:center;padding-top:8px}
.footer p{font-size:10px}
.footer a{display:block;color:var(--white);text-decoration:none;font-size:13px;font-weight:700;margin-top:3px}

.more-bar{position:absolute;top:413px;left:0;width:100%;height:29px;background:linear-gradient(90deg,var(--black),var(--red) 30%,var(--red));color:var(--white);font-size:11px;text-align:center;line-height:29px}
.promo{position:absolute;top:448px;left:0;width:100%;height:326px;background:var(--black)}
.promo__photo{position:absolute;top:33px;left:240px;width:323px;height:250px;background:radial-gradient(circle at 60% 45%,#8a8c93,#3a3c42 55%,#151515)}
.promo__copy{position:absolute;top:70px;left:37px;font-family:'Bebas Neue',sans-serif;color:var(--white);font-size:62px;line-height:0.92;letter-spacing:-1px}
.promo__copy em{font-style:normal;color:var(--red)}
.promo__soon{display:block;font-size:30px;margin-top:8px;letter-spacing:0}
.promo__dots{position:absolute;top:276px;left:268px;display:flex;gap:6px}
.promo__dots span{width:5px;height:5px;border-radius:50%;background:#777}
.promo__dots span:first-child{background:var(--white)}
</style>
</head>
<body>
<div class="spread-label">PAGE 5 &amp; 6</div>

<section class="page page--left">
  <header class="masthead">
    <svg class="masthead__red" width="582" height="88" viewBox="0 0 582 88"><polygon points="0,0 297,0 240,88 0,88" fill="#d0202a"/></svg>
    <div class="brand"><span class="brand__dot"></span>CORVEL</div>
    <div class="contact">
      <span class="contact__title">Please contact us for an official quote:</span>
      <span class="contact__row"><span class="contact__icon"></span>03 5550 1274</span>
      <span class="contact__row"><span class="contact__icon"></span>sam@corvelathletichub.com.au</span>
      <span class="contact__row"><span class="contact__icon"></span>www.corvelathletichub.com.au</span>
    </div>
  </header>
  <div class="title-band"><h1>TEAMWEAR PRICE LIST</h1></div>
  <div class="terms">Prices shown below exclude GST, Custom Clothing is based on order of 20 + units,<br>smaller order quantities are available on request</div>
  <div class="section-head"><span class="section-head__arrow"></span><h2>ACCESSORIES</h2></div>

  <div class="grid">
    <article class="card"><div class="card__name">Soccer Balls<br>Tarro Sports<small>Match Soccer Balls Size 4/5</small></div><div class="card__photo ph-ball" role="img" aria-label="Match soccer ball photo"></div><div class="card__price">$35</div></article>
    <article class="card"><div class="card__name">Soccer Balls<br>Tarro Sports<small>Training Soccer Balls Size 4/5</small></div><div class="card__photo ph-ball" role="img" aria-label="Training soccer ball photo"></div><div class="card__price">$16.<sup>90</sup></div></article>
    <article class="card"><div class="card__name">Training Singlet Bibs<small>7 Colors to choose<br>(S, M, L, or XL)</small></div><div class="card__photo ph-bibs" role="img" aria-label="Stack of coloured training bibs"></div><div class="card__price">$7.<sup>90</sup></div></article>
    <article class="card"><div class="card__name">Whistle</div><div class="card__photo ph-whistle" role="img" aria-label="Whistle photo"></div><div class="card__price">$2</div></article>

    <article class="card"><div class="card__name">Lanyard for<br>Whistle</div><div class="card__photo ph-lanyard" role="img" aria-label="Black whistle lanyard photo"></div><div class="card__price">$2</div></article>
    <article class="card"><div class="card__name">Mini<br>Air Compressor<br>for Balls</div><div class="card__photo ph-comp" role="img" aria-label="Mini air compressor photo"></div><div class="card__price">$195</div></article>
    <article class="card"><div class="card__name">Heavy Duty<br>Air Compressor<br>for Balls</div><div class="card__photo ph-heavy" role="img" aria-label="Heavy duty air compressor photo"></div><div class="card__price">$250</div></article>
    <article class="card"><div class="card__name">Hand Held<br>Ball Pump</div><div class="card__photo ph-pump" role="img" aria-label="Hand held ball pump photo"></div><div class="card__price">$7.<sup>50</sup></div></article>

    <article class="card"><div class="card__name">Ball Carry Bag<small>Holds approximately<br>12 balls</small></div><div class="card__photo ph-net" role="img" aria-label="Mesh ball carry bag photo"></div><div class="card__price">$19.<sup>90</sup></div></article>
    <article class="card"><div class="card__name">Multi Use Kit Bag</div><div class="card__photo ph-kit" role="img" aria-label="Black kit bag photo"></div><div class="card__price">$69</div></article>
    <article class="card"><div class="card__name">Footy Coaches Board<br>Magnetic with<br>Name Magnets</div><div class="card__photo ph-board" role="img" aria-label="Magnetic coaches board photo"></div><div class="card__price">$75</div></article>
    <article class="card"><div class="card__name">Tackle Bag<small>1800 High</small></div><div class="card__photo ph-tackle" role="img" aria-label="Blue tackle bag photo"></div><div class="card__price">$345</div></article>
  </div>

  <footer class="footer">
    <p>View our full range catalogues look at stock "design your own" sublimated garments, etc. from our website:</p>
    <a href="#">www.corvelathletichub.com.au</a>
  </footer>
</section>

<section class="page page--right">
  <header class="masthead">
    <svg class="masthead__red" width="582" height="88" viewBox="0 0 582 88"><polygon points="0,0 297,0 240,88 0,88" fill="#d0202a"/></svg>
    <div class="brand"><span class="brand__dot"></span>CORVEL</div>
    <div class="contact">
      <span class="contact__title">Please contact us for an official quote:</span>
      <span class="contact__row"><span class="contact__icon"></span>03 5550 1274</span>
      <span class="contact__row"><span class="contact__icon"></span>sam@corvelathletichub.com.au</span>
      <span class="contact__row"><span class="contact__icon"></span>www.corvelathletichub.com.au</span>
    </div>
  </header>
  <div class="title-band"><h1>TEAMWEAR PRICE LIST</h1></div>
  <div class="terms">Prices shown below exclude GST, Custom Clothing is based on order of 20 + units,<br>smaller order quantities are available on request</div>
  <div class="section-head"><span class="section-head__arrow"></span><h2>ACCESSORIES</h2></div>

  <div class="grid">
    <article class="card"><div class="card__name">Tackle Bag<small>1500 High</small></div><div class="card__photo ph-tackle" role="img" aria-label="Blue tackle bag photo"></div><div class="card__price">$290</div></article>
    <article class="card"><div class="card__name">Rectangle<br>Bump Bag</div><div class="card__photo ph-bump" role="img" aria-label="Blue rectangle bump bag photo"></div><div class="card__price">$129</div></article>
    <article class="card"><div class="card__name">Ground Markers<small>UFO Shape (6 Colours)</small></div><div class="card__photo ph-cones" role="img" aria-label="Coloured ground marker cones photo"></div><div class="card__price">$1.<sup>80</sup></div></article>
  </div>

  <div class="more-bar">PLUS MANY MORE PRODUCTS AVAILABLE ON REQUEST</div>
  <div class="promo">
    <div class="promo__photo" role="img" aria-label="Athlete in grey training tee with powder burst"></div>
    <div class="promo__copy">GET AHEAD<br>OF THE <em>GAME</em><br>THIS SEASON<span class="promo__soon"><em>CX 45</em> COMING SOON</span></div>
    <div class="promo__dots"><span></span><span></span><span></span><span></span></div>
  </div>

  <footer class="footer">
    <p>View our full range catalogues look at stock "design your own" sublimated garments, etc. from our website:</p>
    <a href="#">www.corvelathletichub.com.au</a>
  </footer>
</section>
</body>
</html>
```